Redesign of business card for Cedar Ridge Mechanical

We are looking for a new design for our business cards for Cedar Ridge Mechanical. We are a plumbing & HVAC construction company, operating on the West Coast of Canada and USA. Logo attached.
Industry/Entity Type
Construction - Plumbing & HVAC
Contact Information for Business Card
Name, address, phone numbers, email, website address
Look and feel
Each slider illustrates characteristics of the customer's brand and the style your logo design should communicate.

```html
<!DOCTYPE html>
<html lang="en">
<head>
<meta charset="utf-8">
<title>Cedar Ridge Mechanical – Business Card</title>
<link href="https://fonts.googleapis.com/css2?family=Montserrat:wght@400;500;700&display=swap" rel="stylesheet">
<style>
  :root {
    --backdrop: #e9e9e9;
    --card-dark: #1c1c1c;
    --card-light: #ffffff;
    --ink: #1a1a1a;
    --ink-soft: #2e2e2e;
    --paper-text: #ffffff;
  }
  * { margin: 0; padding: 0; box-sizing: border-box; }
  html, body {
    width: 1200px; height: 900px; overflow: hidden;
    background: var(--backdrop);
    font-family: "Montserrat", sans-serif;
  }
  .canvas {
    position: relative; width: 1200px; height: 900px;
  }
  .card {
    position: absolute; left: 285px;
    width: 630px; height: 360px;
    border-radius: 26px;
    box-shadow: 0 10px 30px rgba(0,0,0,0.18);
    overflow: hidden;
  }
  .card-front { top: 60px; background: var(--card-dark); }
  .card-back { top: 480px; background: var(--card-light); color: var(--ink); }

  .front-brand {
    position: absolute; inset: 0;
    display: flex; align-items: center; justify-content: center; gap: 14px;
    color: var(--paper-text);
    font-weight: 700; font-size: 30px; letter-spacing: 1px; text-transform: uppercase;
  }
  .brand-square { width: 18px; height: 18px; background: currentColor; }

  .back-brand {
    position: absolute; right: 48px; top: 92px;
    display: flex; align-items: center; gap: 10px;
    font-weight: 700; font-size: 21px; letter-spacing: 0.6px; text-transform: uppercase;
    color: var(--ink);
  }
  .back-brand .brand-square { width: 13px; height: 13px; }

  .person { position: absolute; left: 48px; top: 120px; }
  .person-name { font-weight: 700; font-size: 24px; letter-spacing: 0.5px; }
  .person-title { font-weight: 400; font-size: 14px; margin-top: 2px; }

  .divider {
    position: absolute; left: 48px; right: 48px; top: 178px;
    height: 2px; background: var(--ink);
  }

  .contacts {
    position: absolute; left: 48px; top: 196px;
    list-style: none; font-size: 15px; color: var(--ink-soft);
  }
  .contacts li { display: flex; align-items: center; gap: 10px; height: 26px; }
  .contacts svg { width: 13px; height: 13px; fill: var(--ink); flex: none; }

  .address {
    position: absolute; right: 48px; bottom: 34px;
    font-style: normal; font-size: 15px; line-height: 1.3; color: var(--ink-soft);
  }
</style>
</head>
<body>
<main class="canvas">
  <section class="card card-front" aria-label="Card front">
    <div class="front-brand"><span class="brand-square"></span>Cedar Ridge Mechanical</div>
  </section>

  <section class="card card-back" aria-label="Card back">
    <div class="back-brand"><span class="brand-square"></span>Cedar Ridge Mechanical</div>

    <div class="person">
      <h1 class="person-name">Daniel Hart</h1>
      <p class="person-title">Managing Director</p>
    </div>

    <div class="divider"></div>

    <ul class="contacts">
      <li>
        <svg viewBox="0 0 24 24" aria-hidden="true"><path d="M6.6 10.8a15.1 15.1 0 0 0 6.6 6.6l2.2-2.2c.3-.3.7-.4 1-.2 1.1.4 2.3.6 3.6.6.6 0 1 .4 1 1V20c0 .6-.4 1-1 1A17 17 0 0 1 3 4c0-.6.4-1 1-1h3.5c.6 0 1 .4 1 1 0 1.3.2 2.5.6 3.6.1.3 0 .7-.2 1z"/></svg>
        555.204.7730
      </li>
      <li>
        <svg viewBox="0 0 24 24" aria-hidden="true"><path d="M2 5h20v14H2z M3.5 6.5 12 13l8.5-6.5" fill="none" stroke="#1a1a1a" stroke-width="2"/><path d="M2 5h20l-10 8z"/></svg>
        info@cedarridgemechanical.com
      </li>
      <li>
        <svg viewBox="0 0 24 24" aria-hidden="true"><circle cx="12" cy="12" r="10" fill="none" stroke="#1a1a1a" stroke-width="2"/><path d="M2 12h20M12 2c3 3 3 17 0 20M12 2c-3 3-3 17 0 20" fill="none" stroke="#1a1a1a" stroke-width="1.6"/></svg>
        www.cedarridgemechanical.com
      </li>
    </ul>

    <address class="address">
      240 Birch Hollow Road<br>
      Salem, OR 97301
    </address>
  </section>
</main>
</body>
</html>
```